Verdant Systems Business Card

want the back of card to be blue- with the logo in the center
front of card- info plus logo (info being mailing address, email address, and website address )
4 different names with titles to have on cards
1) Calvin Borsted - Owner
2) Naomi Trelvik- Customer Relationship Specialist
3) Felix Andrade- Vice President of Sales
4) Owen Markby- Chief Technology Officer

Target Market(s)

tech company in the government/probation office industry

Industry/Entity Type

Government Office

Contact Information for Business Card

1) Calvin Borsted - Owner

Colors
0355a3
ffffff

Requirements
Must have
• back side should be blue, with the logo placed in the center
• front side needs to include both the logo, as well as company info (info should include website address, email address, and mailing address)

```html
<!DOCTYPE html>
<html lang="en">
<head>
<meta charset="utf-8">
<title>Verdant Systems Business Card</title>
<link href="https://fonts.googleapis.com/css2?family=Open+Sans:wght@400;600;700&family=Roboto:wght@700&display=swap" rel="stylesheet">
<style>
  :root {
    --navy: #1b2d52;
    --stage: #c5c8cc;
    --paper: #ffffff;
    --ink: #474a50;
    --swoosh-grey: #8a8c90;
  }
  * { margin: 0; padding: 0; box-sizing: border-box; }
  html, body { width: 1200px; height: 900px; overflow: hidden; }
  body { background: var(--stage); position: relative; font-family: "Open Sans", sans-serif; }

  .card-front {
    position: absolute; left: 56px; width: 453px; height: 259px;
    background: var(--paper); border-radius: 22px; overflow: hidden;
    box-shadow: 0 4px 8px rgba(0,0,0,0.35);
  }
  .card-front.first { top: 36px; }
  .card-front.second { top: 327px; }
  .card-front.third { top: 619px; }

  .brand {
    position: absolute; left: 26px; top: 98px; width: 150px;
    display: flex; flex-direction: column; align-items: center; gap: 6px;
  }
  .brand-dot { width: 22px; height: 22px; border-radius: 50%; background: var(--navy); }
  .brand-name {
    font-weight: 700; font-size: 19px; color: var(--navy);
    letter-spacing: 0.5px; text-align: center; line-height: 1.1;
  }

  .divider {
    position: absolute; left: 226px; top: 70px; width: 1.5px; height: 119px;
    background: var(--navy);
  }

  .details { position: absolute; left: 245px; top: 64px; color: var(--ink); }
  .person-name { font-weight: 600; font-size: 14px; color: var(--navy); line-height: 17px; }
  .person-title { font-size: 11.5px; line-height: 16px; }
  .address { font-size: 11.5px; line-height: 13.5px; margin-top: 3px; }
  .contact-list { list-style: none; margin-top: 6px; }
  .contact-list li {
    font-size: 11.5px; line-height: 15px; display: flex; align-items: center; gap: 8px;
  }
  .contact-list svg { width: 8px; height: 8px; fill: var(--navy); flex: none; }

  .swoosh { position: absolute; left: 0; bottom: 0; width: 453px; height: 50px; }

  .card-back {
    position: absolute; left: 584px; top: 296px; width: 567px; height: 323px;
    background: var(--navy); border-radius: 24px;
    box-shadow: 0 4px 10px rgba(0,0,0,0.35);
    display: flex; flex-direction: column; align-items: center; justify-content: center; gap: 14px;
  }
  .card-back .brand-dot { width: 40px; height: 40px; background: var(--paper); }
  .card-back .brand-name { font-size: 38px; color: var(--paper); letter-spacing: 1px; }

  .offer-note {
    position: absolute; left: 575px; top: 720px; width: 600px;
    font-family: "Roboto", sans-serif; font-weight: 700; font-size: 22px;
    line-height: 27px; color: var(--navy);
  }
</style>
</head>
<body>

<svg width="0" height="0" style="position:absolute">
  <defs>
    <symbol id="icon-phone" viewBox="0 0 10 10"><path d="M2 0.5 L3.8 2.6 L2.9 3.6 Q4 5.9 6.4 7.1 L7.4 6.2 L9.5 8 L8.3 9.5 Q3 8.6 0.5 1.7 Z"/></symbol>
    <symbol id="icon-mobile" viewBox="0 0 10 10"><path d="M2.5 0 H7.5 V10 H2.5 Z M3.5 1 V8 H6.5 V1 Z"/></symbol>
    <symbol id="icon-mail" viewBox="0 0 10 10"><path d="M0 2 H10 V8.5 H0 Z M0.8 2.6 L5 5.6 L9.2 2.6 Z"/></symbol>
    <symbol id="icon-globe" viewBox="0 0 10 10"><circle cx="5" cy="5" r="4.8"/></symbol>
    <symbol id="front-swoosh" viewBox="0 0 453 50">
      <path d="M0 32 Q226 -6 453 30" fill="none" stroke="#8a8c90" stroke-width="2.5"/>
      <path d="M0 40 Q226 0 453 38 L453 50 L0 50 Z" fill="#1b2d52"/>
    </symbol>
  </defs>
</svg>

<section class="card-front first">
  <div class="brand"><span class="brand-dot"></span><span class="brand-name">Verdant Systems</span></div>
  <div class="divider"></div>
  <div class="details">
    <p class="person-name">Calvin Borsted</p>
    <p class="person-title">Owner</p>
    <p class="address">Alder Crossing<br>Northfield Park, 2047</p>
    <ul class="contact-list">
      <li><svg><use href="#icon-phone"/></svg>555-214-3087</li>
      <li><svg><use href="#icon-mobile"/></svg>555-430-7261(office)</li>
      <li><svg><use href="#icon-mail"/></svg>info@verdantsystems.co</li>
      <li><svg><use href="#icon-globe"/></svg>www.verdantsystems.co</li>
    </ul>
  </div>
  <svg class="swoosh"><use href="#front-swoosh"/></svg>
</section>

<section class="card-front second">
  <div class="brand"><span class="brand-dot"></span><span class="brand-name">Verdant Systems</span></div>
  <div class="divider"></div>
  <div class="details">
    <p class="person-name">Naomi Trelvik</p>
    <p class="person-title">Customer Relationship Specialist</p>
    <p class="address">Alder Crossing<br>Northfield Park, 2047</p>
    <ul class="contact-list">
      <li><svg><use href="#icon-phone"/></svg>555-214-3087</li>
      <li><svg><use href="#icon-mobile"/></svg>555-430-7261(office)</li>
      <li><svg><use href="#icon-mail"/></svg>info@verdantsystems.co</li>
      <li><svg><use href="#icon-globe"/></svg>www.verdantsystems.co</li>
    </ul>
  </div>
  <svg class="swoosh"><use href="#front-swoosh"/></svg>
</section>

<section class="card-front third">
  <div class="brand"><span class="brand-dot"></span><span class="brand-name">Verdant Systems</span></div>
  <div class="divider"></div>
  <div class="details">
    <p class="person-name">Felix Andrade</p>
    <p class="person-title">Vice President of Sales</p>
    <p class="address">Alder Crossing<br>Northfield Park, 2047</p>
    <ul class="contact-list">
      <li><svg><use href="#icon-phone"/></svg>555-214-3087</li>
      <li><svg><use href="#icon-mobile"/></svg>555-430-7261(office)</li>
      <li><svg><use href="#icon-mail"/></svg>info@verdantsystems.co</li>
      <li><svg><use href="#icon-globe"/></svg>www.verdantsystems.co</li>
    </ul>
  </div>
  <svg class="swoosh"><use href="#front-swoosh"/></svg>
</section>

<section class="card-back">
  <span class="brand-dot"></span>
  <span class="brand-name">Verdant Systems</span>
</section>

<p class="offer-note">I have made this card by using 3 different name . If you want i will make the card 4 different name and provide you all editable and print ready file.</p>

</body>
</html>
```